Varnex Consulting Business card design.

See our website www.varnexconsulting.example which will give you a good idea of what we are about. The font is called 'Play'.

I'd like a standout business card in keeping with the themes and branding on the website

Target Market(s)

professionals. HR directors

Industry/Entity Type

Business

Contact Information for Business Card

Varnex Consulting PO Box 3172 Merrowdale NSW 2291 1300 485 193 Gavin Threlkeld Principal email: career@varnexconsulting.example ABN: 71203948865

Font styles to use
Other font styles liked:
• Play

Requirements
Must have
• Must have same design colours and branding as website.
• On back I'd prefer a list of the things we do which appears below the name at the header on the website

```html
<!DOCTYPE html>
<html lang="en">
<head>
<meta charset="utf-8">
<title>Varnex Consulting – Business Card</title>
<link rel="stylesheet" href="https://fonts.googleapis.com/css2?family=Play:wght@400;700&display=swap">
<style>
  :root {
    --page-bg: #e9e7e3;
    --navy-deep: #0b1d2e;
    --navy-mid: #17304a;
    --navy-light: #24405c;
    --brand-blue: #2a8fd6;
    --ink-dark: #1d2a38;
    --ink-grey: #3c4650;
    --tagline-grey: #b9c3cc;
    --card-white: #ffffff;
    --card-fade: #eeeeee;
  }
  * { margin: 0; padding: 0; box-sizing: border-box; }
  html, body {
    width: 1200px; height: 950px; overflow: hidden;
    background: var(--page-bg);
    font-family: "Play", sans-serif;
  }
  .canvas {
    position: relative; width: 1200px; height: 950px;
    display: flex; flex-direction: column; align-items: center; justify-content: center; gap: 40px;
  }
  .card {
    position: relative; width: 700px; height: 400px;
    box-shadow: 0 10px 28px rgba(0,0,0,0.22);
    overflow: hidden;
  }

  /* Back side */
  .card-back {
    background: linear-gradient(100deg, var(--navy-deep) 0%, var(--navy-mid) 60%, var(--navy-light) 100%);
  }
  .card-back .brand {
    position: absolute; left: 150px; top: 150px;
    font-size: 40px; font-weight: 400; letter-spacing: 3px;
    color: var(--card-white);
  }
  .card-back .services {
    position: absolute; right: 56px; top: 218px;
    font-size: 17px; letter-spacing: 1px; color: var(--tagline-grey);
  }
  .card-back .services .divider { color: var(--brand-blue); margin: 0 8px; }

  /* Front side */
  .card-front {
    background: linear-gradient(160deg, var(--card-white) 55%, var(--card-fade) 100%);
  }
  .card-front .brand {
    position: absolute; left: 64px; top: 58px;
    font-size: 42px; font-weight: 700; letter-spacing: 3px;
    color: var(--ink-dark);
  }
  .accent-bar-left {
    position: absolute; left: 0; top: 150px; width: 16px; height: 140px;
    background: var(--navy-mid);
  }
  .contact {
    position: absolute; left: 56px; top: 160px;
    list-style: none; font-size: 17px; line-height: 25px; color: var(--ink-grey);
  }
  .contact li { display: flex; align-items: center; gap: 8px; }
  .contact .address { padding-left: 26px; }
  .contact svg { width: 16px; height: 16px; fill: var(--ink-dark); flex: none; }
  .person {
    position: absolute; right: 52px; top: 292px; text-align: right;
  }
  .person .name { font-size: 25px; font-weight: 700; color: var(--ink-dark); letter-spacing: 0.5px; }
  .person .role { font-size: 18px; color: var(--brand-blue); margin-top: 2px; }
  .accent-bar-right {
    position: absolute; right: 0; top: 300px; width: 14px; height: 50px;
    background: var(--brand-blue);
  }
</style>
</head>
<body>
<main class="canvas">
  <section class="card card-back" aria-label="Card back">
    <div class="brand">VARNEX CONSULTING</div>
    <div class="services">Coaching<span class="divider">|</span>Leadership<span class="divider">|</span>Outplacement</div>
  </section>

  <section class="card card-front" aria-label="Card front">
    <div class="brand">VARNEX CONSULTING</div>
    <div class="accent-bar-left"></div>
    <ul class="contact">
      <li class="address">PO Box 3172 Merrowdale</li>
      <li class="address">NSW 2291</li>
      <li>
        <svg viewBox="0 0 16 16" aria-hidden="true"><path d="M3 1h3l1 4-2 1.2a9 9 0 0 0 4.8 4.8L11 9l4 1v3a2 2 0 0 1-2 2A12 12 0 0 1 1 3a2 2 0 0 1 2-2z"/></svg>
        1300 485 193
      </li>
      <li>
        <svg viewBox="0 0 16 16" aria-hidden="true"><path d="M1 3h14v10H1z M1.5 3.5 8 9l6.5-5.5" stroke="#fff" stroke-width="1.2"/></svg>
        career@varnexconsulting.example
      </li>
      <li>
        <svg viewBox="0 0 16 16" aria-hidden="true"><circle cx="8" cy="8" r="7"/><path d="M1 8h14M8 1c-3 3.5-3 10.5 0 14M8 1c3 3.5 3 10.5 0 14" stroke="#fff" stroke-width="1" fill="none"/></svg>
        www.varnexconsulting.example
      </li>
    </ul>
    <div class="person">
      <div class="name">Gavin Threlkeld</div>
      <div class="role">Principal</div>
    </div>
    <div class="accent-bar-right"></div>
  </section>
</main>
</body>
</html>
```